Verlindo Magician

I want the business card for my business to give to people who watch that later I will be employed to show magic here is my website http://www.balsamomagicien.com/I want the interesting design , i am very opened for formal and informal, I watch a lot of design so don't stick to the common shape and form but i hope it can also be produced the thing to write on will be the same as in picture that i will upload , i also will upload the logo for you that so can be easy to useDenis CostilleMagicianMAGICIAN BALSAMO 17 rue des Tilleuls - 25000 BESANÇON contact@verlindoillusions.example tel. 0381 946 157 tel. 0674 219 503

```html
<!DOCTYPE html>
<html lang="en">
<head>
<meta charset="utf-8">
<title>Verlindo Magician – Business Card</title>
<link rel="stylesheet" href="https://fonts.googleapis.com/css2?family=Open+Sans:wght@300;400;700&display=swap">
<style>
  :root {
    --canvas-bg: #3b3533;
    --card-white: #f7f7f6;
    --card-black: #111111;
    --ink: #111111;
    --ink-soft: #333333;
    --accent-red: #e8322d;
    --divider: #d4d4d4;
    --logo-light: #e9e9e9;
    --portrait-dark: #1c1c1c;
    --portrait-light: #e6e6e6;
  }
  * { box-sizing: border-box; margin: 0; padding: 0; }
  html, body {
    width: 1200px;
    height: 844px;
    overflow: hidden;
    background: var(--canvas-bg);
    font-family: "Open Sans", Arial, sans-serif;
  }
  .canvas {
    position: relative;
    width: 1200px;
    height: 844px;
    display: flex;
    align-items: center;
    justify-content: center;
    gap: 40px;
  }
  .card {
    width: 520px;
    height: 297px;
    position: relative;
    box-shadow: 0 10px 24px rgba(0,0,0,.45);
  }

  /* Front */
  .card-front {
    background: var(--card-white);
    display: flex;
  }
  .identity {
    width: 238px;
    padding: 26px 0 22px 30px;
    display: flex;
    flex-direction: column;
    align-items: center;
  }
  .portrait {
    width: 170px;
    height: 182px;
    border-radius: 70px 70px 14px 14px;
    background: linear-gradient(180deg, var(--portrait-light) 0%, var(--portrait-dark) 45%, var(--portrait-dark) 100%);
  }
  .wordmark {
    margin-top: 10px;
    font-weight: 300;
    font-size: 24px;
    letter-spacing: 2px;
    color: var(--ink);
    text-align: center;
    line-height: 1.1;
  }
  .wordmark-sub {
    display: block;
    font-size: 9px;
    letter-spacing: 2.5px;
  }
  .divider {
    width: 1px;
    background: var(--divider);
    margin: 32px 0 86px;
  }
  .details {
    padding: 40px 0 0 24px;
    color: var(--ink);
    font-size: 13px;
    line-height: 1.32;
  }
  .person-name {
    font-weight: 700;
    font-size: 17px;
    letter-spacing: .3px;
    line-height: 1.1;
  }
  .person-role {
    color: var(--accent-red);
    font-size: 13px;
    margin-bottom: 2px;
  }
  .contact-list { list-style: none; }
  .contact-list li {
    display: flex;
    align-items: center;
    gap: 6px;
  }
  .contact-list svg { width: 12px; height: 12px; flex: none; }
  .company {
    margin-top: 2px;
    font-weight: 700;
    font-size: 13px;
  }
  .address { color: var(--ink-soft); }

  /* Back */
  .card-back {
    background: var(--card-black);
    display: flex;
    align-items: center;
    justify-content: center;
  }
  .back-wordmark {
    font-weight: 300;
    color: var(--logo-light);
    font-size: 40px;
    letter-spacing: 4px;
    text-align: center;
    line-height: 1.05;
  }
  .back-wordmark .wordmark-sub {
    font-size: 11px;
    letter-spacing: 3px;
  }
</style>
</head>
<body>
<main class="canvas">
  <section class="card card-front" aria-label="Business card front">
    <div class="identity">
      <div class="portrait" role="img" aria-label="Illustration of the magician in a dark jacket holding a playing card"></div>
      <div class="wordmark">VERLINDO<span class="wordmark-sub">MAGICIAN</span></div>
    </div>
    <div class="divider"></div>
    <div class="details">
      <p class="person-name">MARC RAVOULET</p>
      <p class="person-role">Magician</p>
      <ul class="contact-list">
        <li>
          <svg viewBox="0 0 12 12" aria-hidden="true"><path d="M1 4c0-1.5 2-2.5 5-2.5S11 2.5 11 4v1H8.5V3.8H3.5V5H1z M3 6h6l1 4.5H2z" fill="#111"/></svg>
          0381 946 157
        </li>
        <li>
          <svg viewBox="0 0 12 12" aria-hidden="true"><path d="M1 4c0-1.5 2-2.5 5-2.5S11 2.5 11 4v1H8.5V3.8H3.5V5H1z M3 6h6l1 4.5H2z" fill="#111"/></svg>
          0674 219 503
        </li>
        <li>
          <svg viewBox="0 0 12 12" aria-hidden="true"><rect x="0.5" y="2" width="11" height="8" fill="#111"/><path d="M0.5 2.5 6 7l5.5-4.5" fill="none" stroke="#fff" stroke-width="1"/></svg>
          contact@verlindoillusions.example
        </li>
        <li>
          <svg viewBox="0 0 12 12" aria-hidden="true"><circle cx="6" cy="6" r="5.5" fill="#111"/><ellipse cx="6" cy="6" rx="2.2" ry="5.5" fill="none" stroke="#fff" stroke-width=".8"/><path d="M0.5 6h11" stroke="#fff" stroke-width=".8"/></svg>
          www.verlindoillusions.example
        </li>
      </ul>
      <p class="company">MAGICIAN VERLINDO</p>
      <p class="address">17 rue des Tilleuls - 39210<br>MONTREVAL</p>
    </div>
  </section>

  <section class="card card-back" aria-label="Business card back">
    <div class="back-wordmark">VERLINDO<span class="wordmark-sub">MAGICIAN</span></div>
  </section>
</main>
</body>
</html>
```